BrindleStaffing Business Card Design

We are a staffing company finding positions for dedicated nurses and physicians.

Target Market(s)

Business Professionals

Industry/Entity Type

Staffing

Contact Information for Business Card

Gordon Pratley
Chairman
417 39th Avenue South
SAINT PETERSBURG FL 33712
813-555-4172 Mobile
813-555-8036 Fax
gpratley@brindlestaffing.com
www.brindlestaffing.com

Font styles to use
Sans Serif

Colors
fbee3e
f04a50
f37122

Requirements
Must have
• Logo Attached, see colors below. We'd like to see Yellow, Orange and Red.

```html
<!DOCTYPE html>
<html lang="en">
<head>
<meta charset="utf-8">
<title>BrindleStaffing Business Card</title>
<link rel="stylesheet" href="https://fonts.googleapis.com/css2?family=Questrial&family=Roboto:wght@400;700&display=swap">
<style>
  :root {
    --backdrop: #1e1e1e;
    --paper: #ffffff;
    --brand-orange: #f37122;
    --brand-red: #f04a50;
    --brand-yellow: #fbee3e;
    --ink-light: #ffffff;
  }
  * { margin: 0; padding: 0; box-sizing: border-box; }
  html, body {
    width: 1125px; height: 1200px; overflow: hidden;
    background: var(--backdrop);
  }
  .canvas { position: relative; width: 1125px; height: 1200px; }
  .card {
    position: absolute; left: 162px; width: 800px; height: 457px;
  }
  .card--front { top: 113px; background: var(--paper); }
  .card--back { top: 629px; background: var(--brand-red); overflow: hidden; }

  .front__panel {
    position: absolute; left: 424px; top: 0; width: 376px; height: 457px;
    background: var(--brand-orange);
  }
  .wordmark {
    font-family: "Roboto", sans-serif; font-weight: 700;
    letter-spacing: -1px; white-space: nowrap;
  }
  .front__wordmark {
    position: absolute; left: 50px; top: 200px;
    font-size: 52px; line-height: 60px; color: var(--brand-red);
  }
  .front__marker {
    position: absolute; left: 398px; top: 92px; width: 52px; height: 52px;
    background: var(--brand-yellow); border: 3px solid var(--ink-light);
  }
  .contact {
    position: absolute; left: 471px; top: 0;
    font-family: "Questrial", sans-serif; color: var(--ink-light);
  }
  .contact__name { position: absolute; top: 92px; font-size: 30px; white-space: nowrap; letter-spacing: 0.5px; }
  .contact__title { position: absolute; top: 128px; font-size: 19px; letter-spacing: 0.5px; }
  .contact__address { position: absolute; top: 199px; font-size: 18px; line-height: 24px; white-space: nowrap; letter-spacing: 0.3px; }
  .contact__list { position: absolute; top: 260px; list-style: none; }
  .contact__item {
    display: flex; align-items: center; height: 25.5px;
    font-size: 18px; white-space: nowrap; letter-spacing: 0.3px;
  }
  .contact__icon { width: 22px; height: 18px; margin-right: 10px; flex: none; }

  .back__brand { position: absolute; right: 44px; top: 342px; text-align: right; color: var(--ink-light); }
  .back__wordmark { font-size: 44px; line-height: 48px; }
  .back__url {
    font-family: "Roboto", sans-serif; font-size: 18px; letter-spacing: 2.4px;
    margin-top: 4px;
  }
</style>
</head>
<body>
<main class="canvas">
  <section class="card card--front">
    <div class="front__panel"></div>
    <div class="wordmark front__wordmark">BrindleStaffing</div>
    <div class="front__marker"></div>
    <div class="contact">
      <div class="contact__name">Gordon Pratley</div>
      <div class="contact__title">Chairman</div>
      <div class="contact__address">417 39th Avenue South<br>SAINT PETERSBURG FL 33712</div>
      <ul class="contact__list">
        <li class="contact__item">
          <svg class="contact__icon" viewBox="0 0 22 18" aria-hidden="true"><rect x="6" y="0" width="10" height="18" rx="1.5" fill="none" stroke="#fff" stroke-width="2"/><rect x="9.5" y="14" width="3" height="2" fill="#fff"/></svg>
          813-555-4172
        </li>
        <li class="contact__item">
          <svg class="contact__icon" viewBox="0 0 22 18" aria-hidden="true"><rect x="6" y="1" width="10" height="6" fill="#fff"/><rect x="1" y="7" width="20" height="8" rx="1.5" fill="#fff"/><rect x="5" y="12" width="12" height="5" fill="#fff" stroke="#f37122" stroke-width="1"/></svg>
          813-555-8036
        </li>
        <li class="contact__item">
          <svg class="contact__icon" viewBox="0 0 22 18" aria-hidden="true"><rect x="2" y="4" width="18" height="12" fill="#fff"/><path d="M2 4 L11 11 L20 4" fill="none" stroke="#f37122" stroke-width="1.5"/></svg>
          gpratley@brindlestaffing.com
        </li>
        <li class="contact__item">
          <svg class="contact__icon" viewBox="0 0 22 18" aria-hidden="true"><circle cx="11" cy="9" r="8" fill="#fff"/><path d="M3 9 H19 M11 1 V17" fill="none" stroke="#f37122" stroke-width="1.4"/></svg>
          www.brindlestaffing.com
        </li>
      </ul>
    </div>
  </section>

  <section class="card card--back">
    <div class="back__brand">
      <div class="wordmark back__wordmark">BrindleStaffing</div>
      <div class="back__url">www.brindlestaffing.com</div>
    </div>
  </section>
</main>
</body>
</html>
```